Beef cattle farm needs signs which can be seen from roadside

We would like submissions of artwork for a sign that will hang from a fence or gate and will be seen by passing cars.

Existing logo and branding theme for the company is attached.

Signage can be between 900mm x 400mm - 1200mm x 600mm

Industry/Entity Type

Farm

Requirements
Must have
• the Signs should have the following information:
• Company name: Wendlow Grazing Company
• Address: 417 Corrigan Flat Road
• Contact number: 0431 862 407
• email address: admin@wendlowgrazingcompany.com.au
• - Logo and branding as per attached artwork

```html
<!DOCTYPE html>
<html lang="en">
<head>
<meta charset="utf-8">
<title>Wendlow Grazing Company – Roadside Sign</title>
<link rel="stylesheet" href="https://fonts.googleapis.com/css2?family=Montserrat:wght@500&family=Arimo:wght@400;700&display=swap">
<style>
  :root {
    --backdrop: #858583;
    --sign-white: #ffffff;
    --brand-green: #14603a;
    --brand-green-dark: #053b22;
    --brand-green-light: #136b38;
    --brand-grey: #6d6e71;
    --swoosh-grey: #a9abae;
    --cow-brown: #b5602a;
    --cow-cream: #efe3d6;
    --text-light: #ffffff;
  }
  html, body {
    margin: 0;
    width: 1200px;
    height: 655px;
    overflow: hidden;
    background: var(--backdrop);
  }
  .sign {
    position: absolute;
    left: 110px;
    top: 110px;
    width: 980px;
    height: 435px;
    background: var(--sign-white);
    overflow: hidden;
  }
  .sign__band {
    position: absolute;
    inset: 0;
  }
  .brand__disc {
    position: absolute;
    left: 48px;
    top: 85px;
    width: 200px;
    height: 200px;
    border-radius: 50%;
    background: var(--brand-green);
  }
  .brand__name {
    position: absolute;
    left: 288px;
    top: 128px;
    width: 392px;
    margin: 0;
    font-family: "Montserrat", sans-serif;
    font-weight: 500;
    line-height: 1;
    white-space: nowrap;
  }
  .brand__name-main {
    display: block;
    font-size: 63px;
    letter-spacing: 0.5px;
    color: var(--brand-green);
  }
  .brand__name-sub {
    display: block;
    margin-top: 10px;
    font-size: 36px;
    letter-spacing: 0.3px;
    color: var(--brand-grey);
  }
  .cattle-photo {
    position: absolute;
    left: 690px;
    top: 20px;
    width: 290px;
    height: 275px;
    border-radius: 45% 0 0 30%;
    background: radial-gradient(ellipse at 35% 45%, var(--cow-cream) 0 18%, var(--cow-brown) 45%, #c97a44 70%, var(--cow-cream) 100%);
  }
  .contact {
    font-family: "Arimo", sans-serif;
    color: var(--text-light);
    position: absolute;
    margin: 0;
    white-space: nowrap;
  }
  .contact--phone {
    left: 58px;
    top: 372px;
    font-size: 31px;
    font-weight: 700;
  }
  .contact--address {
    right: 46px;
    top: 347px;
    font-size: 23px;
    font-weight: 400;
  }
  .contact--email {
    right: 42px;
    top: 380px;
    font-size: 21.5px;
    font-weight: 700;
  }
</style>
</head>
<body>
  <main class="sign">
    <div class="brand__disc"></div>
    <h1 class="brand__name">
      <span class="brand__name-main">WENDLOW</span>
      <span class="brand__name-sub">GRAZING COMPANY</span>
    </h1>

    <div class="cattle-photo" role="img" aria-label="Photograph of a brown and white cow looking toward the viewer"></div>

    <svg class="sign__band" width="980" height="435" viewBox="0 0 980 435" aria-hidden="true">
      <defs>
        <linearGradient id="bandGreen" x1="0" y1="0" x2="1" y2="0">
          <stop offset="0" stop-color="var(--brand-green-dark)"/>
          <stop offset="1" stop-color="var(--brand-green-light)"/>
        </linearGradient>
      </defs>
      <path class="swoosh" fill="var(--swoosh-grey)"
            d="M0,278 C120,330 230,348 380,325 C560,296 760,250 900,258 C940,261 965,270 980,276 L980,290 C900,268 760,268 560,305 C400,335 230,352 0,292 Z"/>
      <path class="band" fill="url(#bandGreen)"
            d="M0,290 C230,352 400,337 560,307 C760,270 900,270 980,292 L980,435 L0,435 Z"/>
    </svg>

    <p class="contact contact--phone">Call : 0431 862 407</p>
    <p class="contact contact--address">417 Corrigan Flat Road</p>
    <p class="contact contact--email">admin@wendlowgrazingcompany.com.au</p>
  </main>
</body>
</html>
```